Website Homepage re-design Project

I run a large format poster printing business & have a website hosted on vantrelstore using one of their templates, http://www.brimlowprints.co.uk
I am looking to update the home page to give it a more professional look, it must be clear for our clients to choose their poster type from the homepage
The design must contain the 5 poster type categories as well as most of the information above the poster categories, most of the text below the green "terms & conditions" footer can be left as it is as it's used for keywords, maybe just tidied up a bit
I would like to keep the customer reviews & sample posters on the home page along with the quick glance (fly-out) poster prices
I would also like the 4 step ordering process graphic updated, ie where it say "Select Poster Type" "Choose Poster Size" etc, there are 4 variations of this graphic which I will need to insert in their respective pages
If something can be done with the company name "Brimlow Prints & Sealers" that would be great.
I would prefer a design which shows all the information down to the section where it says "Order Your Poster Here" displayed on the screen when the page is loaded

```html
<!DOCTYPE html>
<html lang="en">
<head>
<meta charset="utf-8">
<title>Brimlow Prints &amp; Sealers – Poster Printing &amp; Laminating</title>
<link href="https://fonts.googleapis.com/css2?family=Gelasio:wght@400&family=Source+Sans+3:wght@400;600&display=swap" rel="stylesheet">
<style>
:root{
  --ink:#333;
  --muted:#555;
  --gold:#e0a93a;
  --red:#a42a2a;
  --red-bright:#c0392b;
  --page:#f3f3f3;
  --panel:#e4e4e4;
  --head-top:#4a4a4a;
  --head-bot:#2b2b2b;
  --nav:#141414;
  --foot:#e8e8e8;
  --bar:#2c2c2c;
  --white:#fff;
}
*{box-sizing:border-box;margin:0;padding:0}
html,body{width:969px;height:1200px;overflow:hidden}
body{position:relative;background:var(--page);font-family:"Source Sans 3",Arial,sans-serif;color:var(--ink);font-size:12px}
.abs{position:absolute}
.nowrap{white-space:nowrap}
.site-header{left:0;top:0;width:969px;height:88px;background:linear-gradient(var(--head-top),var(--head-bot))}
.brand{left:44px;top:18px;display:flex;align-items:center;gap:10px;color:var(--white);font-size:17px;line-height:22px}
.brand-mark{width:40px;height:40px;background:var(--gold)}
.currency{left:710px;top:14px;color:#ddd;font-size:11.5px;display:flex;align-items:center;gap:10px;white-space:nowrap}
.currency-select{background:#3a3a3a;border-radius:3px;padding:3px 8px;display:flex;align-items:center;gap:6px;width:130px}
.flag{width:14px;height:10px;background:#c9c9c9}
.account-links{left:705px;top:50px;font-size:11.5px;color:#ccc;white-space:nowrap}
.account-links .hl{color:var(--gold)}
.main-nav{left:0;top:88px;width:969px;height:52px;background:var(--nav);box-shadow:0 3px 6px rgba(0,0,0,.4)}
.main-nav a{position:absolute;top:0;height:52px;line-height:48px;color:#eee;font-size:13.5px;text-decoration:none;white-space:nowrap}
.main-nav .active{left:35px;width:74px;text-align:center;background:linear-gradient(#5a5a5a,#3a3a3a);color:var(--gold)}
.login{left:812px;top:10px;width:120px;height:30px;background:#2b2b2b;border-radius:3px;color:var(--gold);font-size:13px;display:flex;align-items:center;gap:8px;padding-left:8px;white-space:nowrap}
.login i{width:16px;height:18px;background:#b88a55;border-radius:3px}
.hero{left:40px;top:155px;width:890px;height:297px;background:var(--white);border:1px solid #ddd;box-shadow:0 2px 4px rgba(0,0,0,.08)}
.hero-stage{left:17px;top:18px;width:854px;height:251px;background:radial-gradient(circle at 20% 50%,#fff,#ececec);border:1px solid #ddd}
.hero h1{left:78px;top:60px;font-family:"Gelasio",Georgia,serif;font-weight:400;font-size:28px;color:#3c3c3c;white-space:nowrap}
.hero .sub{left:79px;top:103px;font-size:15px;color:var(--red)}
.btn{position:absolute;height:24px;line-height:24px;border-radius:4px;color:var(--white);font-size:13px;text-align:center;box-shadow:0 1px 2px rgba(0,0,0,.4)}
.btn-dark{left:275px;top:158px;width:73px;background:#444}
.btn-red{left:359px;top:158px;width:82px;background:var(--red-bright)}
.printer-art{left:524px;top:60px;width:266px;height:186px;background:linear-gradient(#2b2b2b 0 30%,#d84c6e 30% 78%,#3a3a3a 78%)}
.dots{left:24px;top:277px;display:flex;gap:8px}
.dots span{width:8px;height:8px;border-radius:50%;background:#888}
.dots span:first-child{background:#333}
.order-panel{left:40px;top:474px;width:421px;height:242px;background:var(--panel);box-shadow:0 3px 5px rgba(0,0,0,.15)}
.step{position:absolute;top:22px;width:62px;height:55px;background:var(--white);box-shadow:0 1px 3px rgba(0,0,0,.25);text-align:center;color:#777;font-size:14px;line-height:16px;padding-top:8px}
.step b{display:block;font-weight:400;font-size:23px;line-height:26px}
.step.on{color:var(--red)}
.step-label{position:absolute;top:87px;width:110px;text-align:center;font-size:12.5px;line-height:14px;color:#666}
.step-label.on{color:var(--red)}
.progress{left:27px;top:133px;width:358px;height:28px;background:var(--red);padding:3px;display:flex;gap:2px}
.progress span{flex:0 0 68px;background:#aaa;color:var(--white);font-size:12px;text-align:center;line-height:22px;white-space:nowrap}
.progress .cur{background:#555}
.progress .go{flex:0 0 72px;background:var(--red-bright);border:1px solid #e99;font-size:13px}
.order-title{left:0;width:421px;top:180px;text-align:center;font-size:17px;color:#444}
.order-hint{left:0;width:421px;top:210px;text-align:center;font-size:12px;color:#555}
.price-badge{left:361px;top:176px;width:54px;height:54px;border-radius:50%;background:var(--gold);border:3px solid var(--white);box-shadow:0 1px 3px rgba(0,0,0,.3);color:var(--red);font-size:10.5px;line-height:11px;text-align:center;padding-top:12px;transform:rotate(-15deg)}
.sample-art{left:72px;top:743px;width:158px;height:223px;background:linear-gradient(135deg,#9fcf7a,#2f7a26);box-shadow:0 2px 5px rgba(0,0,0,.3)}
.sample-caption{left:72px;top:976px;width:152px;text-align:center;font-size:13px}
.we-create{left:255px;top:762px;color:var(--red);font-size:14px}
.create-list{left:258px;top:791px;list-style:none;font-size:14px;color:#555}
.create-list li{height:27.6px;display:flex;gap:10px;white-space:nowrap}
.create-list li::before{content:"➜";color:#444;font-size:11px;line-height:19px}
.create-list .strong{color:#222}
.dispatch{left:477px;top:486px;width:452px;font-size:13px;line-height:21px;color:#444;text-indent:22px}
.product{position:absolute;left:477px;width:448px}
.product h2{font-weight:400;font-size:15px;color:var(--red);display:flex;align-items:center;gap:8px;height:22px;white-space:nowrap}
.product h2 i{width:22px;height:22px;border-radius:50%;background:radial-gradient(#c0392b,#7a1d1d);position:relative;flex:0 0 22px}
.product h2 i::after{content:"";position:absolute;left:7px;top:6px;border-left:9px solid var(--white);border-top:5px solid transparent;border-bottom:5px solid transparent}
.product p{margin:8px 0 0 29px;font-size:11px;line-height:16.5px;color:#333;text-align:justify}
.site-footer{left:0;top:1008px;width:969px;height:122px;background:var(--foot)}
.foot-title{font-size:14px;color:#333}
.testi{left:51px;top:18px;width:340px;font-size:11.5px;line-height:17px;white-space:nowrap}
.rating{display:inline-flex;gap:3px;margin-left:4px;vertical-align:middle}
.rating span{width:6px;height:6px;border-radius:50%;background:#999}
.rating span:first-child{background:#444}
.divider{left:397px;top:12px;width:1px;height:96px;background:#888}
.contact{left:420px;top:18px;font-size:11px;line-height:17px;white-space:nowrap}
.bottom-bar{left:0;top:1130px;width:969px;height:70px;background:var(--bar);color:var(--white);font-size:11px;white-space:nowrap}
.socials{left:759px;top:27px;display:flex;gap:13px}
.socials span{width:21px;height:21px;border-radius:3px}
</style>
</head>
<body>

<header class="site-header abs">
  <div class="brand abs"><span class="brand-mark"></span><span>Brimlow Prints &amp;<br>Sealers</span></div>
  <div class="currency abs">Select Currency <span class="currency-select"><span class="flag"></span>United Kingdom ▾</span></div>
  <div class="account-links abs">My Account &nbsp;| &nbsp;My Cart : <span class="hl">( 0 ) Items</span> &nbsp;| &nbsp;<span class="hl">Check Out</span></div>
</header>

<nav class="main-nav abs">
  <a class="active">Home</a>
  <a style="left:124px">About Us</a>
  <a style="left:209px">Colour Calibration</a>
  <a style="left:343px">Customer Comments</a>
  <a style="left:493px">View Cart</a>
  <a style="left:580px">Contact Us</a>
  <a style="left:674px">FAQ</a>
  <a style="left:732px">Search
    <svg width="14" height="14" viewBox="0 0 14 14" style="vertical-align:-2px;margin-left:3px"><circle cx="6" cy="6" r="4.5" fill="none" stroke="#eee" stroke-width="1.8"/><line x1="9.3" y1="9.3" x2="13" y2="13" stroke="#eee" stroke-width="2"/></svg></a>
  <div class="login abs"><i></i>Customer Login</div>
</nav>

<section class="hero abs">
  <div class="hero-stage abs">
    <h1 class="abs">Poster Printing &amp; Laminating</h1>
    <p class="sub abs">Photo Quality Posters at Fly Poster Prices</p>
    <span class="btn btn-dark">View Prices</span>
    <span class="btn btn-red">Order Now</span>
    <div class="printer-art abs" role="img" aria-label="Large format printer producing a colourful frog poster"></div>
  </div>
  <div class="dots abs"><span></span><span></span><span></span><span></span><span></span></div>
</section>

<section class="order-panel abs">
  <div class="step on" style="left:27px">Step<b>1</b></div>
  <div class="step" style="left:125px">Step<b>2</b></div>
  <div class="step" style="left:223px">Step<b>3</b></div>
  <div class="step" style="left:321px">Step<b>4</b></div>
  <div class="step-label on" style="left:3px">Select<br>Poster Type</div>
  <div class="step-label" style="left:101px">Choose<br>Poster Size</div>
  <div class="step-label" style="left:201px">Upload<br>Your File</div>
  <div class="step-label" style="left:298px">Check Out<br>Pay for Your Poster</div>
  <div class="progress abs"><span class="cur">Selection</span><span>Choosing</span><span>Upload</span><span>Check Out</span><span class="go">Order Now</span></div>
  <div class="order-title abs">Order Your Poster Here</div>
  <div class="order-hint abs">Select your Poster type below &amp; upload your file</div>
  <div class="price-badge abs">Poster<br>Prices</div>
</section>

<div class="sample-art abs" role="img" aria-label="Wild life poster sample showing a cartoon frog"></div>
<div class="sample-caption abs">Wild Life Poster</div>
<div class="we-create abs">We Create...</div>
<ul class="create-list abs">
  <li>Scientific Posters</li>
  <li>Medical Posters</li>
  <li>University Posters</li>
  <li>Regent College Posters</li>
  <li>Menu Posters</li>
  <li class="strong">Wild Life Posters</li>
</ul>

<p class="dispatch abs">Orders placed before 2pm are sent out the same day with either standard delivery @£4.50+vat or Swiftline next day delivery @ £9.50+vat to anywhere in the UK</p>

<article class="product" style="top:543px"><h2><i></i>Matt Photo Paper</h2><p>Photo Quality Poster printing, Printed at 2400 dpi on 180gsm Silk Matt Photo paper, perfect for high quality presentations &amp; matt photo reproduction, these poster will show the finest details</p></article>
<article class="product" style="top:636px"><h2><i></i>Poster with Gloss Encapsulating</h2><p>Photo Quality Poster printing &amp; Laminating. Printed at 2400 dpi &amp; Laminated on both sides with a 5mm edge seal, the Gloss finish enhances the colours. Weatherproof &amp; durable, these posters are ideal for long term use</p></article>
<article class="product" style="top:729px"><h2><i></i>Gloss Photo Paper</h2><p>Photo Quality Poster Printing, Printed at 2400 dpi on 190gsm Gloss Photo paper, perfect for high quality presentations &amp; photographic prints with vivid true to life colours.</p></article>
<article class="product" style="top:822px"><h2><i></i>Poster with Matt Encapsulating</h2><p>Photo Quality Poster printing &amp; Laminating. Printed at 2400dpi &amp; Laminated on both sides with a 5mm edge seal, the Matt finish reduces light reflection. Weatherproof &amp; durable, these posters are ideal for long term use</p></article>
<article class="product" style="top:915px"><h2><i></i>Student Presentation Poster</h2><p>Photo Quality Poster Printing, Printed at 1200dpi on 170gsm High Resolution coated paper, this printing option is ideally suited to students presentations</p></article>

<footer class="site-footer abs">
  <div class="testi abs">
    <div class="foot-title" style="margin-bottom:10px">Testimonials</div>
    <div>Reviewer: Maya <span style="margin-left:64px">Rating :</span><span class="rating"><span></span><span></span><span></span><span></span><span></span></span></div>
    <div style="margin-top:3px">Just got my poster 15 minutes ago. Ordered yesterday around 11-12.<br>Very fast and the poster is amazing! Many thanks! Maya</div>
  </div>
  <div class="divider abs"></div>
  <div class="contact abs">
    <div class="foot-title" style="margin-bottom:8px">Contact Us</div>
    <div class="abs" style="left:0;top:24px">Address :</div>
    <div class="abs" style="left:54px;top:24px">Brimlow Prints &amp; Sealers<br>Nant Y Fedw<br>Hillside Lane, Pontgarreg<br>Llanfarren</div>
    <div class="abs" style="left:186px;top:24px;text-align:right;width:66px">Telephone :<br>Mobile :<br>Fax :</div>
    <div class="abs" style="left:261px;top:26px;line-height:19px">01632 960241<br>07700 900 418<br>01632 960587</div>
    <div class="abs" style="left:359px;top:24px">E - Mail : tom@brimlowprints.co.uk</div>
    <div class="abs" style="left:399px;top:66px">www.brimlowprints.co.uk</div>
  </div>
</footer>

<div class="bottom-bar abs">
  <div class="abs" style="left:40px;top:29px">Copyright © 2012 www.brimlowprintsandsealers.com &nbsp;&nbsp; All rights reserved</div>
  <div class="abs" style="left:673px;top:29px">Connect with us :</div>
  <div class="socials abs">
    <span style="background:#3b5a98"></span><span style="background:#3aa7dc"></span><span style="background:#e2661d"></span><span style="background:#1f74b0"></span><span style="background:#d8d8d8"></span>
  </div>
</div>

</body>
</html>
```